Barrister at Law needs Business Card Design

Need a business card design for Barrister at Law. Double sided. Simple Neil Thorsby and Barrister at Law on one side with contact details on the other side. I would like a professional design using Black or Platinum. Details on reverse side would include qualifications - Bcom-Llb and Acc Spec Commercial Litigation. I have attached the logo. Contact details would include address/ Po Box/ Phone/Fax/Mobile/email. I would like to use raised print or spot gloss.

```html
<!DOCTYPE html>
<html lang="en">
<head>
<meta charset="utf-8">
<title>Neil Thorsby – Barrister at Law business card</title>
<link rel="stylesheet" href="https://fonts.googleapis.com/css2?family=Questrial&family=Open+Sans:wght@400;600&display=swap">
<style>
  :root {
    --backdrop: #2b2d31;
    --card: #3e3e40;
    --silver: #e4e4e6;
    --silver-dim: #b9babd;
    --seal: #4a4a4d;
    --blue: #1f7fc4;
    --white: #f3f3f3;
    --mark-grey: #a9aaad;
  }
  * { box-sizing: border-box; margin: 0; padding: 0; }
  html, body { width: 1200px; height: 864px; overflow: hidden; }
  body {
    background: var(--backdrop);
    display: flex;
    flex-direction: column;
    align-items: center;
    justify-content: center;
    gap: 64px;
  }
  .card {
    position: relative;
    width: 525px;
    height: 300px;
    background: var(--card);
    border-radius: 3px;
    box-shadow: 0 10px 28px rgba(0,0,0,.45);
    overflow: hidden;
  }

  /* Front */
  .card-front { display: flex; align-items: center; justify-content: center; }
  .card-front .seal {
    position: absolute;
    width: 190px; height: 190px;
    left: 50%; top: 50%;
    transform: translate(-50%, -50%);
    border-radius: 50%;
    border: 2px solid var(--seal);
  }
  .front-title {
    position: relative;
    text-align: center;
    font-family: "Questrial", "Century Gothic", sans-serif;
    font-size: 31px;
    line-height: 1.18;
    letter-spacing: .5px;
    color: var(--silver);
    text-shadow: 0 1px 0 rgba(0,0,0,.35);
  }
  .front-title .amp { font-size: 26px; display: block; }

  /* Back */
  .card-back { font-family: "Open Sans", Arial, sans-serif; color: var(--white); }
  .identity { position: absolute; left: 30px; top: 26px; }
  .name { color: var(--blue); font-weight: 600; font-size: 18px; }
  .name .quals { font-size: 11px; margin-left: 3px; }
  .specialty { font-size: 13px; margin-top: 1px; }
  .address { position: absolute; left: 30px; top: 118px; font-size: 13px; line-height: 1.25; }
  .contacts { position: absolute; left: 24px; top: 168px; list-style: none; font-size: 13px; }
  .contacts li { display: flex; align-items: center; gap: 9px; height: 20px; }
  .contacts svg { width: 11px; height: 11px; fill: var(--blue); flex: none; }
  .brand {
    position: absolute;
    right: 28px; bottom: 40px;
    display: flex; align-items: center; gap: 10px;
    color: var(--mark-grey);
    font-size: 17px; font-weight: 600;
  }
  .brand .dot { width: 14px; height: 14px; border-radius: 50%; background: var(--blue); }
</style>
</head>
<body>
  <section class="card card-front" aria-label="Card front">
    <div class="seal" aria-hidden="true"></div>
    <h1 class="front-title">Neil Thorsby<span class="amp">&amp;</span>Barrister at Law</h1>
  </section>

  <section class="card card-back" aria-label="Card back">
    <div class="identity">
      <p class="name">Neil Thorsby<span class="quals">Bcom, LLB</span></p>
      <p class="specialty">Acc Spec Commercial Litigation</p>
    </div>
    <p class="address">14 Quay Chambers Lane<br>Brisbane, QLD 4000</p>
    <ul class="contacts">
      <li><svg viewBox="0 0 12 12"><path d="M2 1h3l1 3-1.5 1a7 7 0 0 0 2.5 2.5L8 6l3 1v3c0 1-1 1-1 1A10 10 0 0 1 1 2s0-1 1-1z"/></svg>(07) 3555 0142</li>
      <li><svg viewBox="0 0 12 12"><path d="M3 1h5v3H3zM1 5h10v6H1zM3 7h6v1H3z"/></svg>07 3555 0143</li>
      <li><svg viewBox="0 0 12 12"><path d="M1 3h10v7H1zM1 3l5 4 5-4v1L6 8 1 4z"/></svg>clerk@thorsbychambers.com</li>
      <li><svg viewBox="0 0 12 12"><path d="M4 8l4-4 1 1-4 4zM1 9l3-3 1 1-3 3zM7 3l3-3 1 1-3 3z"/></svg>www.thorsbychambers.com</li>
    </ul>
    <div class="brand"><span class="dot" aria-hidden="true"></span>Thorsby Chambers</div>
  </section>
</body>
</html>
```